web page design with coding

We are a start up insurance agency who needs to design a full functional web page. we recently did a postcard design though drawkettle I will upload the final project for you to see the color scheme/font we would like to continue to use. I also have a rough draft of verbage I would like our website to have. I will upload that as well.

Reason: I am sorry but the person who will make the final decision on the website is out of the country at the moment and will make the final decision when he returns.

Industry/Entity Type

Insurance

Coding

Coded - Design and coding required

```html
<!DOCTYPE html>
<html lang="en">
<head>
<meta charset="utf-8">
<title>Corvale Insurance Group</title>
<link href="https://fonts.googleapis.com/css2?family=Lora:wght@400;600&family=Open+Sans:wght@700;800&family=Roboto:wght@400;500&family=Roboto+Condensed:wght@400&display=swap" rel="stylesheet">
<style>
:root{
  --navy:#262840;
  --footer:#3a3b52;
  --footer-line:#4a4b62;
  --orange:#f15a24;
  --green:#3bd14b;
  --ink:#1c1c1c;
  --muted:#6a6a6a;
  --band:#f1f1f1;
  --panel:#dcdcdc;
  --white:#ffffff;
}
*{margin:0;padding:0;box-sizing:border-box}
html,body{width:761px;height:1200px;overflow:hidden;background:var(--white)}
body{position:relative;font-family:'Roboto',sans-serif;color:var(--ink)}
.abs{position:absolute}
.serif{font-family:'Lora',serif}

/* header */
.brand{left:102px;top:18px;width:110px;font-family:'Lora',serif;font-weight:600;color:var(--navy);font-size:22px;line-height:22px}
.brand small{display:block;font-size:9px;line-height:12px;font-weight:600;margin-top:4px}
.connect{left:476px;top:14px;font-size:6px;color:#9a9a9a;letter-spacing:.3px}
.socials{display:flex;gap:4px}
.socials span{width:13px;height:13px;border-radius:50%;display:block}
.s1{background:#5b79c4}.s2{background:#1da1f2}.s3{background:#e62117}.s4{background:#3b5ca8}
.head-social{left:476px;top:26px}
.calltoday{left:587px;top:16px;font-size:6px;color:#9a9a9a;letter-spacing:.3px}
.head-phone{left:587px;top:25px;font-family:'Roboto Condensed',sans-serif;font-size:14px;color:var(--navy)}
.head-phone-icon{left:564px;top:23px}
.nav{left:271px;top:54px;display:flex;align-items:center;font-size:7.2px;color:#222}
.nav a{color:inherit;text-decoration:none;margin-right:16px}
.nav .active{background:var(--navy);color:#fff;padding:4px 9px;margin-right:17px}

/* hero */
.hero{left:0;top:78px;width:761px;height:274px;background:linear-gradient(100deg,#f0a247 0%,#d5a869 25%,#a99b82 50%,#8a948f 75%,#7d8c8f 100%)}
.hero-title{left:103px;top:272px;font-family:'Open Sans',sans-serif;font-weight:800;font-size:24px;line-height:28px;color:#fff;letter-spacing:.3px}
.dots{left:345px;top:329px;display:flex;gap:9px;align-items:center}
.dots span{width:5px;height:5px;border-radius:50%;background:#fff}
.dots .on{width:8px;height:8px;background:transparent;border:1.5px solid #fff}
.quote{left:490px;top:112px;width:171px;height:216px;background:rgba(70,68,72,.82);padding:12px 16px}
.quote h2{font-family:'Open Sans',sans-serif;font-weight:800;font-size:12px;color:#fff;letter-spacing:.5px;margin-bottom:6px}
.field{background:#fff;height:22px;margin-bottom:6px;font-size:6px;color:#444;padding:7px 8px}
.typebox{background:#fff;height:48px;padding:8px 8px;font-size:5.6px;color:#333}
.radios{display:flex;gap:12px;margin-top:6px}
.radio{display:flex;gap:4px;align-items:flex-start;line-height:7px}
.radio i{width:9px;height:9px;border:1px solid #777;border-radius:50%;display:block;flex:none}
.quote-btn{margin-top:7px;height:28px;background:var(--orange);color:#fff;font-family:'Open Sans',sans-serif;font-weight:800;font-size:8.5px;text-align:center;line-height:28px;letter-spacing:.4px}

/* feature strip */
.feat{top:365px;height:69px;background:var(--navy);color:#fff;padding:14px 10px 0 50px}
.feat h3{font-family:'Lora',serif;font-weight:600;font-size:11px;margin-bottom:4px}
.feat p{font-size:5.6px;line-height:9px;color:#d8d8e0}
.feat .big{font-family:'Roboto Condensed',sans-serif;color:var(--orange);font-size:16px}
.feat svg{position:absolute;left:16px;top:17px}

/* welcome */
.welcome-h{left:102px;top:454px;font-size:12px;font-weight:600}
.copy{font-size:6.4px;line-height:11.5px;color:var(--muted)}
.w1{left:102px;top:477px;width:203px;text-align:justify}
.w2{left:102px;top:545px;width:318px}
.inline-brand{left:322px;top:479px;width:93px;height:55px;border:1px solid #bbb;font-family:'Lora',serif;font-weight:600;color:var(--navy);font-size:15px;line-height:17px;padding:10px 8px;text-align:center}
.inline-brand small{display:block;font-size:7px;line-height:10px}
.btn-dark{background:#000;color:#fff;font-size:6px;font-weight:500;padding:0 8px;height:15px;line-height:15px;display:flex;align-items:center;gap:5px;letter-spacing:.3px}
.rm1{left:104px;top:576px}
.news{left:104px;top:612px;width:314px;height:169px;background:var(--panel);padding:12px 14px}
.news h3{font-size:11.5px;font-weight:600;margin-bottom:14px}
.item{display:flex;gap:14px;padding-bottom:8px}
.item + .item{border-top:1px solid #cfcfcf;padding-top:10px}
.item .bullet{width:10px;height:10px;background:#000;flex:none;margin-top:2px;display:flex;align-items:center;justify-content:center}
.item h4{font-size:6.8px;font-weight:500;margin-bottom:5px}
.item p{font-size:6px;line-height:10.4px;color:var(--muted);text-align:justify}
.photo{background:linear-gradient(135deg,#8fae5a,#c9cf9a 55%,#6e8f49)}
.p1{left:434px;top:454px;width:224px;height:95px}
.p2{left:434px;top:624px;width:225px;height:94px;background:linear-gradient(180deg,#9ebad6 0%,#c7d4de 45%,#c8a98a 65%,#4f6b3a 100%)}
.card-t{font-size:9.5px}
.card-p{font-size:6px;line-height:9.6px;color:var(--muted);width:224px}
.rm2{left:436px;top:596px}
.rm3{left:436px;top:765px}

/* band */
.band{left:0;top:803px;width:761px;height:143px;background:var(--band)}
.tick-card{top:818px;height:114px;background:#fff;text-align:center;font-size:7px;line-height:12px;color:#333;padding-top:18px}
.tick-card svg{display:block;margin:0 auto 16px}

/* cta */
.cta{left:0;top:946px;width:761px;height:102px;background:var(--navy)}
.cta h2{position:absolute;left:0;width:761px;top:20px;text-align:center;font-family:'Lora',serif;font-weight:400;color:#fff;font-size:16px}
.cta-btn{top:1000px;height:28px;width:98px;color:#fff;font-family:'Open Sans',sans-serif;font-weight:800;font-size:9.5px;letter-spacing:1.6px;text-align:center;line-height:28px}

/* footer */
.footer{left:0;top:1048px;width:761px;height:152px;background:var(--footer)}
.f-brand{left:103px;top:1071px;width:75px;height:46px;border:1px solid #9a9aa8;background:#f2f2f2;font-family:'Lora',serif;font-weight:600;color:var(--navy);font-size:12px;line-height:13px;padding:7px 4px;text-align:center}
.f-brand small{display:block;font-size:5.6px;line-height:8px}
.foot-social{left:110px;top:1134px}
.f-h{font-family:'Open Sans',sans-serif;font-weight:700;font-size:7px;color:#fff;letter-spacing:.2px}
.f-list{font-size:5.6px;line-height:12px;color:#e4e4ea}
.f-input{left:501px;top:1089px;width:158px;height:25px;background:#4c4d64;font-size:5.6px;color:#dcdce4;display:flex;align-items:center;gap:6px;padding-left:10px}
.f-btn{left:595px;top:1122px;width:63px;height:20px;background:var(--orange);color:#fff;font-family:'Open Sans',sans-serif;font-weight:800;font-size:7.5px;text-align:center;line-height:20px}
.f-rule{left:102px;top:1172px;width:556px;height:1px;background:var(--footer-line)}
.copyright{left:470px;top:1184px;width:188px;text-align:right;font-size:5px;color:#d0d0d8}
</style>
</head>
<body>

<header>
  <div class="abs brand">Corvale<small>Corvale Insurance Group</small></div>
  <div class="abs connect">CONNECT WITH US</div>
  <div class="abs socials head-social" aria-label="Social links"><span class="s1"></span><span class="s2"></span><span class="s3"></span><span class="s4"></span></div>
  <svg class="abs head-phone-icon" width="16" height="16" viewBox="0 0 16 16"><circle cx="8" cy="8" r="8" fill="#262840"/><path d="M5 4.2c.5-.4 1-.3 1.3.2l.8 1.2c.2.4.1.8-.2 1l-.6.4c.4 1 1.3 1.9 2.3 2.3l.4-.6c.2-.3.6-.4 1-.2l1.2.8c.5.3.6.8.2 1.3-.7.9-1.8 1-2.9.4C6.9 10.1 5.5 8.7 4.8 7.1 4.3 6 4.3 4.9 5 4.2z" fill="#fff"/></svg>
  <div class="abs calltoday">CALL TODAY FOR YOUR</div>
  <div class="abs head-phone">(555) 310 4827</div>
  <nav class="abs nav">
    <a class="active">Home</a><a>About Us</a><a>Products and Services</a><a>Business Insurance</a><a>Personal Insurance</a><a style="margin-right:0">Contact Us</a>
  </nav>
</header>

<section>
  <div class="abs hero" role="img" aria-label="Photo: a father teaching his young son to ride a bicycle on a country road at sunset"></div>
  <div class="abs hero-title">PERSONAL<br>INSURANCE</div>
  <div class="abs dots"><span></span><span class="on"></span><span></span><span></span><span></span></div>
  <form class="abs quote">
    <h2>GET A QUOTE</h2>
    <div class="field">Name</div>
    <div class="field">E mail</div>
    <div class="field">Phone</div>
    <div class="typebox">SELECT TYPE OF INSURANCE
      <div class="radios">
        <div class="radio"><i></i><span>Commercial<br>Insurance</span></div>
        <div class="radio"><i></i><span>Personal<br>Insurance</span></div>
      </div>
    </div>
    <div class="quote-btn">GET A QUOTE</div>
  </form>
</section>

<section>
  <div class="abs feat" style="left:102px;width:181px">
    <svg width="22" height="22" viewBox="0 0 22 22"><path d="M11 2a5 5 0 0 0-5 5c0 4 5 9 5 9s5-5 5-9a5 5 0 0 0-5-5z" fill="none" stroke="#fff" stroke-width="1.6"/><circle cx="11" cy="7" r="1.8" fill="#fff"/><ellipse cx="11" cy="18" rx="8" ry="2.5" fill="none" stroke="#fff" stroke-width="1.4"/></svg>
    <h3>Find a Location</h3>
    <p>Contrary to popular belief, Lorem Ipsum is not simply random text. It has roots.</p>
  </div>
  <div class="abs feat" style="left:290px;width:181px">
    <svg width="22" height="22" viewBox="0 0 22 22"><path d="M2 8c0-3 4-4 9-4s9 1 9 4v1.5h-4V7.5H6v2H2z" fill="#fff"/><rect x="4" y="10" width="14" height="9" rx="2" fill="#fff"/><circle cx="11" cy="14.5" r="2.6" fill="#262840"/><circle cx="11" cy="14.5" r="1" fill="#fff"/></svg>
    <h3 style="font-size:11.5px">Call us Now Today!</h3>
    <div class="big">(555) 310 4827</div>
  </div>
  <div class="abs feat" style="left:478px;width:180px">
    <svg width="22" height="22" viewBox="0 0 22 22"><circle cx="8" cy="7" r="3.3" fill="#fff"/><circle cx="15" cy="8" r="2.6" fill="#fff"/><path d="M1.5 18c0-4 3-6 6.5-6s6.5 2 6.5 6z" fill="#fff"/><path d="M14 12.5c3 0 6 1.5 6 5h-4.5" fill="#fff"/></svg>
    <h3>Who we are</h3>
    <p>Contrary to popular belief, Lorem Ipsum is not simply random text. It has roots.</p>
  </div>
</section>

<main>
  <h2 class="abs serif welcome-h">Welcome to our site</h2>
  <p class="abs copy w1">Corvale Insurance Group has joined with regional &amp; national insurance companies to provide quality products and superior service. We take the time to discuss options and coverages, not to just sell insurance products. We strive to educate you in the decision making process to become an informed consumer.</p>
  <div class="abs inline-brand">Corvale<small>Corvale Insurance Group</small></div>
  <p class="abs copy w2">We specialize in commercial business &amp; personal insurance. We are committed to providing personal attention to all your insurance needs</p>
  <div class="abs btn-dark rm1">READ MORE <svg width="4" height="5" viewBox="0 0 4 5"><path d="M0 0l4 2.5L0 5z" fill="#fff"/></svg></div>

  <div class="abs news">
    <h3 class="serif">Recent News</h3>
    <div class="item">
      <div class="bullet"><svg width="4" height="5" viewBox="0 0 4 5"><path d="M0 0l4 2.5L0 5z" fill="#fff"/></svg></div>
      <div><h4>Corvale Insurance Group has joined with regional &amp; national</h4>
      <p>There are many variations of passages of Lorem Ipsum available, but the majority have suffered&nbsp; alteration in some form.by injected humour, or randomised words which don't .</p></div>
    </div>
    <div class="item">
      <div class="bullet"><svg width="4" height="5" viewBox="0 0 4 5"><path d="M0 0l4 2.5L0 5z" fill="#fff"/></svg></div>
      <div><h4>The standard chunk of Lorem Ipsum used since.</h4>
      <p>At vero eos et accusamus et iusto odio dignissimos ducimus qui blanditiis praesentium voluptatum deleniti atque. corrupti quos dolores et quas molestias excepturi .</p></div>
    </div>
  </div>

  <div class="abs photo p1" role="img" aria-label="Photo: a smiling family of three outdoors in a green park"></div>
  <h3 class="abs serif card-t" style="left:434px;top:557px">Personal Insurance</h3>
  <p class="abs card-p" style="left:434px;top:570px">Corvale Insurance Group is a one stop shop for all of your personal and business insurance needs</p>
  <div class="abs btn-dark rm2">READ MORE</div>

  <div class="abs photo p2" role="img" aria-label="Photo: a city skyline of high-rise towers behind a line of trees"></div>
  <h3 class="abs serif card-t" style="left:434px;top:727px">Busniess Insurance</h3>
  <p class="abs card-p" style="left:434px;top:740px">Corvale Insurance Group is a one stop shop for all of your personal and business insurance needs</p>
  <div class="abs btn-dark rm3">READ MORE</div>
</main>

<section>
  <div class="abs band"></div>
  <div class="abs tick-card" style="left:104px;width:190px">
    <svg width="30" height="30" viewBox="0 0 30 30"><path d="M26 10A13 13 0 1 1 22 5" fill="none" stroke="#f15a24" stroke-width="1.8"/><path d="M9 14l5 5L27 5" fill="none" stroke="#f15a24" stroke-width="1.8"/></svg>
    Hurricane Season is around the corner, this<br>is the best time to make sure you have all<br>the coverage you need
  </div>
  <div class="abs tick-card" style="left:296px;width:178px">
    <svg width="30" height="30" viewBox="0 0 30 30"><path d="M26 10A13 13 0 1 1 22 5" fill="none" stroke="#f15a24" stroke-width="1.8"/><path d="M9 14l5 5L27 5" fill="none" stroke="#f15a24" stroke-width="1.8"/></svg>
    Auto? Home? Life?<br>are you and your family fully covered?
  </div>
  <div class="abs tick-card" style="left:475px;width:183px">
    <svg width="30" height="30" viewBox="0 0 30 30"><path d="M26 10A13 13 0 1 1 22 5" fill="none" stroke="#f15a24" stroke-width="1.8"/><path d="M9 14l5 5L27 5" fill="none" stroke="#f15a24" stroke-width="1.8"/></svg>
    Coverage you deserve, rates you can afford,<br>all from an agency you can trust.
  </div>
</section>

<section class="abs cta">
  <h2>Are you looking for Insurance?</h2>
</section>
<div class="abs cta-btn" style="left:281px;background:var(--orange)">BUSINESS</div>
<div class="abs cta-btn" style="left:386px;background:var(--green)">PERSONAL</div>

<footer>
  <div class="abs footer"></div>
  <div class="abs f-brand">Corvale<small>Corvale Insurance Group</small></div>
  <div class="abs socials foot-social" aria-label="Social links"><span class="s1"></span><span class="s2"></span><span class="s3"></span><span class="s4"></span></div>

  <h4 class="abs f-h" style="left:231px;top:1070px">CONTACT US</h4>
  <div class="abs f-list" style="left:231px;top:1085px">1200 Larkfield Avenue<br>Springdale, MD 20011<br>1.800.555.0142<br>hello@corvalegroup.com</div>

  <h4 class="abs f-h" style="left:369px;top:1070px">MENU</h4>
  <div class="abs f-list" style="left:369px;top:1085px">Home<br>About Us<br>Products and Services<br>Business Insurance<br>Personal Insurance<br>Contact Us</div>

  <h4 class="abs f-h" style="left:501px;top:1070px">NEWSLETTER SIGNUP!</h4>
  <div class="abs f-input"><svg width="7" height="5" viewBox="0 0 7 5"><rect width="7" height="5" fill="#dcdce4"/><path d="M0 0l3.5 2.7L7 0" fill="none" stroke="#4c4d64" stroke-width=".8"/></svg>E mail id</div>
  <div class="abs f-btn">SIGNUP!</div>

  <div class="abs f-rule"></div>
  <div class="abs copyright">Copyrights@ 2016 All Rights Reserved</div>
</footer>

</body>
</html>
```